Business Card Design for Flood Rescue 360 - Property Restoration Professionals

I need a business card designed for Flood Rescue 360. We are a full-service property restoration solution. Providing water, fire, smoke & storm restoration as well as mold remediation and full remodel or reconstruction to homes and businesses across Dallas-Fort Worth, TX.
Target Market(s)
home and business owners with insurance covered property damage from water, fire or storm related damage
Industry/Entity Type
property restoration
Contact Information for Business Card
Marcus Pelley General Manager Cell: 214-555-0193 Office: 469-555-0148 email: Marcus@FloodRescue360.example services: Water, Fire, Mold, Reconstruction Tagline: Urgency for Your Water Emergency!
Look and feel
Each slider illustrates characteristics of the customer's brand and the style your logo design should communicate.

```html
<!DOCTYPE html>
<html lang="en">
<head>
<meta charset="utf-8">
<title>Flood Rescue 360 – Business Card</title>
<link rel="stylesheet" href="https://fonts.googleapis.com/css2?family=Montserrat:wght@400;500;700;800&display=swap">
<style>
  :root {
    --brand-blue: #14aee0;
    --brand-grey: #7a7a7a;
    --paper: #f4f4f4;
    --ink: #2b2b2b;
    --card-dark: #262626;
    --backdrop: #1b1b1b;
    --on-dark: #f2f2f2;
  }
  * { box-sizing: border-box; margin: 0; padding: 0; }
  html, body { width: 1200px; height: 1059px; overflow: hidden; }
  body {
    background: var(--backdrop);
    font-family: "Montserrat", sans-serif;
    position: relative;
  }
  .card {
    position: absolute;
    border-radius: 20px;
    overflow: hidden;
  }
  .card-front { left: 257px; top: 89px; width: 687px; height: 390px; background: var(--paper); }
  .card-back  { left: 254px; top: 547px; width: 693px; height: 393px; background: var(--card-dark); }

  .wordmark {
    display: flex; align-items: center;
    color: var(--brand-blue);
    font-weight: 800;
    text-transform: uppercase;
  }
  .wordmark-name { line-height: 0.98; letter-spacing: -0.5px; white-space: nowrap; }
  .wordmark-ring { border: 6px solid var(--brand-grey); border-radius: 50%; flex: none; }

  .card-front .wordmark { position: absolute; left: 34px; top: 164px; font-size: 29px; gap: 12px; }
  .card-front .wordmark-ring { width: 46px; height: 46px; border-width: 5px; }

  .divider { position: absolute; left: 321px; top: 110px; width: 1px; height: 169px; background: var(--brand-grey); }

  .contact { position: absolute; left: 347px; top: 106px; color: var(--ink); }
  .contact-name { color: var(--brand-blue); font-weight: 700; font-size: 28px; letter-spacing: 0.3px; line-height: 1.1; }
  .contact-role { font-size: 17px; font-weight: 400; }
  .contact-list { list-style: none; margin-top: 17px; }
  .contact-list li { display: flex; align-items: center; gap: 8px; font-size: 17px; height: 28px; letter-spacing: 0.2px; }
  .contact-list svg { width: 12px; height: 12px; fill: var(--brand-blue); flex: none; }

  .wave { position: absolute; left: 0; bottom: 0; width: 687px; height: 390px; }

  .card-back .wordmark { position: absolute; left: 0; right: 0; top: 126px; justify-content: center; font-size: 52px; gap: 18px; }
  .card-back .wordmark-ring { width: 84px; height: 84px; border-width: 8px; }

  .services, .tagline {
    position: absolute; left: 0; right: 0; text-align: center;
    color: var(--on-dark); font-size: 18px; letter-spacing: 0.4px;
  }
  .services { top: 314px; }
  .services .dot { color: var(--brand-blue); margin: 0 8px; }
  .tagline { top: 342px; }
</style>
</head>
<body>

<section class="card card-front" aria-label="Business card front">
  <svg class="wave" viewBox="0 0 687 390" aria-hidden="true">
    <path d="M420 348 Q560 358 687 345 L687 352 Q560 364 420 350 Z" fill="var(--brand-grey)"/>
    <path d="M0 300 Q250 365 470 360 Q600 362 687 357 L687 390 L0 390 Z" fill="var(--brand-blue)"/>
  </svg>

  <div class="wordmark">
    <div class="wordmark-name">Flood<br>Rescue 360</div>
    <span class="wordmark-ring"></span>
  </div>

  <div class="divider"></div>

  <div class="contact">
    <h1 class="contact-name">MARCUS PELLEY</h1>
    <p class="contact-role">General Manager</p>
    <ul class="contact-list">
      <li><svg viewBox="0 0 12 12"><path d="M1 5 Q6 0 11 5 L9 6 L8 4.5 Q6 4 4 4.5 L3 6 Z M2 7 H10 V11 H2 Z"/></svg>469-555-0148</li>
      <li><svg viewBox="0 0 12 12"><path d="M3 0 H9 Q10 0 10 1 V11 Q10 12 9 12 H3 Q2 12 2 11 V1 Q2 0 3 0 Z M3.5 1.5 V9.5 H8.5 V1.5 Z"/></svg>214-555-0193</li>
      <li><svg viewBox="0 0 12 12"><path d="M0 4 L6 0 L12 4 V12 H0 Z M1 4.5 L6 8 L11 4.5 L6 1.2 Z"/></svg>Marcus@FloodRescue360.example</li>
      <li><svg viewBox="0 0 12 12"><circle cx="6" cy="6" r="6"/><path d="M3 3 Q5 4 4 6 Q6 7 5 10 Q8 8 7 6 Q9 5 8 2 Z" fill="var(--paper)"/></svg>www.FloodRescue360.example</li>
    </ul>
  </div>
</section>

<section class="card card-back" aria-label="Business card back">
  <div class="wordmark">
    <div class="wordmark-name">Flood<br>Rescue 360</div>
    <span class="wordmark-ring"></span>
  </div>
  <p class="services">Water<span class="dot">•</span>Fire<span class="dot">•</span>Mold<span class="dot">•</span>Reconstruction</p>
  <p class="tagline">Urgency for Your Water Emergency!</p>
</section>

</body>
</html>
```